Upscale business cards needed for Board of Directors

We need professional business cards created for members of our family business Board of Directors. We would like these relatively simple and straightforward, but also with a unique element to set them apart. Probably stick with neutral and simple colors - white, grey etc. We need space for the traditional elements, including name, title, address, email/phone number. And we will be creating several from this template so it needs to be template that is easy to switch information in and out of.
Business
See description

```html
<!DOCTYPE html>
<html lang="en">
<head>
<meta charset="utf-8">
<title>Corvale Holdings – Business Card</title>
<link rel="stylesheet" href="https://fonts.googleapis.com/css2?family=Arimo:wght@400;700&display=swap">
<style>
  :root {
    --page-bg: #d8d5d1;
    --card-bg: #eef0ef;
    --card-edge: #c9cccb;
    --ink: #1f1f1f;
    --ink-soft: #3a3a3a;
    --title-gold: #8a7a55;
    --rule-gold: #7d6a45;
    --band-dark: #161616;
    --band-mid: #262626;
    --brand-silver: #e4e4e2;
  }
  * { margin: 0; padding: 0; box-sizing: border-box; }
  html, body {
    width: 1200px; height: 969px; overflow: hidden;
    background: var(--page-bg);
    font-family: "Arimo", Arial, sans-serif;
  }
  .business-card {
    position: absolute; left: 100px; top: 202px;
    width: 1000px; height: 564px;
    background: var(--card-bg);
    border: 1px solid var(--card-edge);
    box-shadow: 0 10px 30px rgba(0,0,0,.12);
  }
  .divider-rule {
    position: absolute; left: 129px; top: 58px;
    width: 4px; height: 446px; background: var(--rule-gold);
  }
  .icon { position: absolute; left: 70px; width: 26px; height: 26px; fill: var(--ink-soft); }
  .icon-person { top: 102px; }
  .icon-pin { top: 245px; }
  .icon-phone { top: 378px; }
  .icon-mail { top: 414px; }
  .icon-web { top: 452px; }
  .contact-text { position: absolute; left: 167px; color: var(--ink-soft); font-size: 25px; line-height: 36px; white-space: nowrap; }
  .person-name { position: absolute; left: 167px; top: 82px; font-size: 33px; font-weight: 700; color: var(--ink); white-space: nowrap; }
  .person-title { position: absolute; left: 167px; top: 124px; font-size: 27px; color: var(--title-gold); }
  .address { top: 226px; }
  .phone { top: 374px; }
  .email { top: 414px; }
  .website { top: 450px; }
  .brand-band {
    position: absolute; right: 0; top: 0;
    width: 260px; height: 100%;
    background: linear-gradient(90deg, var(--band-dark), var(--band-mid));
    display: flex; flex-direction: column; align-items: center; justify-content: center;
    gap: 16px;
  }
  .brand-square {
    width: 28px; height: 28px; background: var(--brand-silver);
  }
  .brand-name {
    color: var(--brand-silver);
    font-family: "Arimo", Arial, sans-serif;
    font-weight: 700;
    font-size: 22px;
    line-height: 28px;
    white-space: nowrap;
  }
</style>
</head>
<body>
  <div class="business-card">
    <div class="divider-rule"></div>

    <svg class="icon icon-person" viewBox="0 0 24 24" aria-hidden="true">
      <circle cx="12" cy="7" r="5"/>
      <path d="M2 24c0-6 4.5-9 10-9s10 3 10 9z"/>
    </svg>
    <p class="person-name">MARTIN HALE</p>
    <p class="person-title">President</p>

    <svg class="icon icon-pin" viewBox="0 0 24 24" aria-hidden="true">
      <path d="M12 1a8 8 0 0 0-8 8c0 6 8 14 8 14s8-8 8-14a8 8 0 0 0-8-8zm0 11a3 3 0 1 1 0-6 3 3 0 0 1 0 6z"/>
    </svg>
    <p class="contact-text address">2147 Ashcombe Lane<br>Linden Grove, NY 10987</p>

    <svg class="icon icon-phone" viewBox="0 0 24 24" aria-hidden="true">
      <path d="M3 8c0-3 4-5 9-5s9 2 9 5v2h-5V8H8v2H3z"/>
      <path d="M5 12h14l2 9H3z"/>
    </svg>
    <p class="contact-text phone">555 0134 2290</p>

    <svg class="icon icon-mail" viewBox="0 0 24 24" aria-hidden="true">
      <path d="M2 5h20v14H2z"/>
      <path d="M3 6l9 7 9-7" fill="none" stroke="var(--card-bg)" stroke-width="1.6"/>
    </svg>
    <p class="contact-text email">martin@corvale.com</p>

    <svg class="icon icon-web" viewBox="0 0 24 24" aria-hidden="true">
      <circle cx="12" cy="12" r="10"/>
      <path d="M2 12h20M12 2c3 3 3 17 0 20M12 2c-3 3-3 17 0 20" fill="none" stroke="var(--card-bg)" stroke-width="1.4"/>
    </svg>
    <p class="contact-text website">www.corvale.com</p>

    <div class="brand-band">
      <div class="brand-square" aria-hidden="true"></div>
      <p class="brand-name">Corvale Holdings</p>
    </div>
  </div>
</body>
</html>
```